New website for a business that provides Steady Steps Clinic

A new website that details the services that are provided around Steady Steps Clinic for people with a disability through QPKV. There also needs to incorporate an about us and a staff page, Plus a referral form that is a google doc.
The business already has a web address that needs to be tailored.
Soft colours are preferred.
Do not have lots of pictures, keep them minimal.
A logo for the business is also needed to be incorporated, and this is a separate project that can be awarded to the website winner.
Website needs to be able to be used on WIX who will be the host for the design.

Target Market(s)

QPKV clients requiring behaviour support clician

Industry/Entity Type

Clinical behaviour support and analysis

Colors
00AB8E
00BBA5
67D7C9
C6EFE9
E9F9F6

Requirements
Must have
• Soft colours, preferable pale turquoise, minimal pictures, clean, sophisticated and classical look

```html
<!DOCTYPE html>
<html lang="en">
<head>
<meta charset="utf-8">
<title>Steady Steps Clinic</title>
<link href="https://fonts.googleapis.com/css2?family=Playfair+Display:wght@400;600;700;800&family=Kumbh+Sans:wght@400;500;600;700&display=swap" rel="stylesheet">
<style>
:root{
  --green:#00AB8E;
  --green-2:#00BBA5;
  --mint:#67D7C9;
  --pale:#C6EFE9;
  --paler:#E9F9F6;
  --ink:#111111;
  --text:#555a5f;
  --black:#0b0b0b;
  --soft:#f6f7f7;
}
*{margin:0;padding:0;box-sizing:border-box}
html,body{width:1200px;height:4231px;overflow:hidden}
body{font-family:'Kumbh Sans',sans-serif;color:var(--text);background:#fff;position:relative}
.serif{font-family:'Playfair Display',serif}
section,header,footer{position:absolute;left:0;width:1200px}
.abs{position:absolute}
.btn{position:absolute;display:flex;align-items:center;justify-content:center;font-size:15px;font-weight:600;height:41px}
.btn-fill{background:var(--green);color:#fff}
.btn-line{border:2px solid var(--green);color:var(--green);background:#fff}
.center{text-align:center;left:0;width:1200px}

.topbar{top:0;height:48px;background:var(--black)}
.topbar .strip{position:absolute;left:0;top:0;height:48px;width:808px;background:var(--green);clip-path:polygon(0 0,100% 0,97% 100%,0 100%)}
.topbar .item{position:absolute;top:16px;font-size:11px;color:#fff;display:flex;align-items:center;gap:8px}
.follow{position:absolute;right:112px;top:10px;display:flex;align-items:center;gap:10px;color:#fff;font-size:15px}
.dot{width:28px;height:28px;border-radius:50%;background:var(--green);display:inline-block}

.nav{top:48px;height:100px;background:#fff;border-bottom:1px solid #e6e6e6}
.wordmark{font-family:'Kumbh Sans',sans-serif;font-weight:700}
.brand{position:absolute;left:112px;top:30px;font-size:31px;color:var(--ink)}
.menu{position:absolute;top:42px;font-size:14px;color:#444}

.hero{top:148px;height:622px;background:linear-gradient(180deg,#1e2540 0%,#2a2d4a 55%,#4a3b55 80%,#0d0d14 100%)}
.hero-art{position:absolute;right:0;top:0;width:560px;height:622px;background:radial-gradient(ellipse at 55% 45%,rgba(180,190,230,.35),rgba(30,37,64,0) 65%)}
.hero h1{position:absolute;left:103px;top:86px;font-size:72px;line-height:87px;font-weight:800;color:#fff;width:620px}
.hero h1 span{color:var(--green-2)}
.hero p{position:absolute;left:103px;top:364px;width:680px;font-size:23px;line-height:48px;color:#fff}
.btn-ghost{border:2px solid #fff;color:#fff}

.features{top:770px;height:330px;background:var(--soft);box-shadow:0 10px 20px rgba(0,0,0,.05)}
.feature{position:absolute;top:0;width:300px;height:330px;text-align:center}
.feature + .feature{border-left:1px solid var(--pale)}
.f-icon{position:absolute;left:110px;top:60px;width:80px;height:80px;border-radius:50%;background:#fff;box-shadow:0 4px 14px rgba(0,0,0,.06);display:flex;align-items:center;justify-content:center}
.feature h3{position:absolute;top:152px;width:100%;font-size:15px;font-weight:700;color:var(--ink)}
.feature p{position:absolute;top:186px;left:40px;width:220px;font-size:12.5px;line-height:23px}

.about{top:1231px;height:630px}
.about h2{position:absolute;left:660px;top:32px;font-size:56px;line-height:68px;font-weight:700;color:var(--ink);width:460px}
.lead{position:absolute;left:660px;top:185px;font-size:17px;font-weight:600;color:var(--green)}
.about .body{position:absolute;left:660px;top:226px;width:430px;font-size:15.5px;line-height:30px}
.ticks{position:absolute;left:660px;top:396px;list-style:none}
.ticks li{height:38px;display:flex;align-items:center;gap:12px;font-size:15.5px}
.about .know{position:absolute;left:660px;top:526px;font-size:16px;line-height:30px;color:#222}

.offer{top:1960px;height:760px}
h2.title{position:absolute;font-size:56px;font-weight:700;color:var(--ink)}
.sub{position:absolute;font-size:18.5px;line-height:33px;color:#666}
.card{position:absolute;top:202px;width:310px;height:435px;background:#fff;box-shadow:0 6px 24px rgba(0,0,0,.07)}
.card .photo{height:235px}
.card .c-icon{position:absolute;left:34px;top:200px;width:76px;height:76px;border-radius:50%;background:var(--green);display:flex;align-items:center;justify-content:center}
.card h3{position:absolute;left:33px;top:292px;font-size:20px;font-weight:500;color:var(--ink)}
.card p{position:absolute;left:33px;top:328px;width:250px;font-size:12.5px;line-height:26px}
.card a{position:absolute;left:33px;top:389px;font-size:13.5px;color:var(--green);text-decoration:underline}

.band{top:2796px;height:346px;background:linear-gradient(90deg,#00a88c,#14b39a 50%,#00a88c)}
.band h2{position:absolute;font-size:56px;font-weight:700;color:#fff;top:52px}
.band p{position:absolute;top:143px;font-size:16px;line-height:33px;color:#fff}
.btn-white{background:#fff;color:var(--green)}

.team{top:3200px;height:620px}
.member{position:absolute;top:177px;width:237px;height:300px;background:#fff;box-shadow:0 6px 24px rgba(0,0,0,.07);text-align:center}
.member .photo{height:202px}
.pill{position:absolute;left:54px;top:186px;width:129px;height:32px;border-radius:16px;background:#fff;box-shadow:0 2px 8px rgba(0,0,0,.1);display:flex;align-items:center;justify-content:center;gap:16px}
.pill i{width:16px;height:16px;border-radius:50%;background:#cfd3d3;display:block}
.member h3{position:absolute;top:232px;width:100%;font-size:19px;font-weight:500;color:var(--ink)}
.member span{position:absolute;top:264px;left:0;width:100%;font-size:12.5px;color:var(--green)}

.footer{top:3876px;height:355px;background:var(--black);color:#fff}
.footer .f-brand{position:absolute;left:112px;top:68px;font-size:28px}
.footer p{font-size:13px;line-height:25px}
.footer h4{position:absolute;top:68px;font-size:19px;font-weight:700}
.footer ul{position:absolute;top:112px;list-style:none;font-size:13px;line-height:32px}
.fsoc{position:absolute;top:235px;width:30px;height:30px;border-radius:50%;background:var(--green)}
.email{position:absolute;left:875px;top:189px;width:212px;height:33px;background:#fff;color:#999;font-size:11px;padding:11px 14px}
.subscribe{position:absolute;left:875px;top:236px;width:212px;height:31px;background:var(--green);font-size:13px;font-weight:600;display:flex;align-items:center;justify-content:center}
.copy{position:absolute;top:311px;font-size:12px}
</style>
</head>
<body>

<header class="topbar">
  <div class="strip"></div>
  <div class="item" style="left:112px"><svg width="11" height="11" viewBox="0 0 12 12"><circle cx="6" cy="6" r="5" fill="none" stroke="#fff" stroke-width="1.5"/><path d="M6 3v3l2 1.5" stroke="#fff" stroke-width="1.3" fill="none"/></svg>Mon - Fri 8:00 - 6:30</div>
  <div class="item" style="left:271px"><svg width="9" height="12" viewBox="0 0 10 14"><path d="M5 0a5 5 0 0 0-5 5c0 4 5 9 5 9s5-5 5-9a5 5 0 0 0-5-5z" fill="#fff"/><circle cx="5" cy="5" r="2" fill="#00AB8E"/></svg>14 Willow Lane, Ardent 318 204</div>
  <div class="item" style="left:525px"><svg width="9" height="12" viewBox="0 0 10 14"><path d="M5 0a5 5 0 0 0-5 5c0 4 5 9 5 9s5-5 5-9a5 5 0 0 0-5-5z" fill="#fff"/><circle cx="5" cy="5" r="2" fill="#00AB8E"/></svg>Contact Number: +1 555 010 2030</div>
  <div class="follow">Follow Us <span class="dot"></span><span class="dot"></span><span class="dot"></span></div>
</header>

<header class="nav">
  <div class="brand wordmark">Steady Steps Clinic</div>
  <span class="menu" style="left:534px">Home</span>
  <span class="menu" style="left:637px">About Us</span>
  <span class="menu" style="left:763px">Our Team</span>
  <span class="menu" style="left:893px">Reviews</span>
  <span class="menu" style="left:1011px">Contact Us</span>
</header>

<section class="hero" role="img" aria-label="Night sky with a person lifting a glowing puzzle piece into a brain outline">
  <div class="hero-art"></div>
  <h1 class="serif">The <span>right care</span> when you need it most</h1>
  <p>Sed quia consequuntur magni dolores eos qui ratione volup sequi nesciunt. Neque porro tempora incidunt</p>
  <a class="btn btn-fill" style="left:103px;top:484px;width:206px">Book An Appointment</a>
  <a class="btn btn-ghost" style="left:330px;top:484px;width:140px">Referral Form</a>
</section>

<section class="features">
  <div class="feature" style="left:0">
    <div class="f-icon"><svg width="40" height="40" viewBox="0 0 40 40" fill="none" stroke="#00AB8E" stroke-width="1.6"><rect x="14" y="8" width="20" height="14" rx="5"/><path d="M18 22l-2 5 6-5"/><rect x="5" y="17" width="14" height="11" rx="4"/><path d="M9 28l-1 4 5-4"/></svg></div>
    <h3 class="serif">Actual teachings of great</h3>
    <p>Lorem ipsum dolor sit amet, consectetur adipiscing elit, sed do eiusmod tempor incididunt ut labore et dolore</p>
  </div>
  <div class="feature" style="left:300px">
    <div class="f-icon"><svg width="40" height="40" viewBox="0 0 40 40" fill="none" stroke="#00AB8E" stroke-width="1.6"><path d="M20 6c-8 0-12 6-12 12 0 5 3 8 6 10v6h12v-6c3-2 6-5 6-10 0-6-4-12-12-12z"/><path d="M20 12v16M15 18h10"/></svg></div>
    <h3 class="serif">Actual teachings of great</h3>
    <p>Lorem ipsum dolor sit amet, consectetur adipiscing elit, sed do eiusmod tempor incididunt ut labore et dolore</p>
  </div>
  <div class="feature" style="left:600px">
    <div class="f-icon"><svg width="40" height="40" viewBox="0 0 40 40" fill="none" stroke="#00AB8E" stroke-width="1.6"><circle cx="20" cy="9" r="4"/><circle cx="10" cy="22" r="4"/><circle cx="30" cy="22" r="4"/><circle cx="20" cy="22" r="3"/><path d="M4 34c0-4 3-6 6-6s6 2 6 6M24 34c0-4 3-6 6-6s6 2 6 6"/></svg></div>
    <h3 class="serif">Actual teachings of great</h3>
    <p>Lorem ipsum dolor sit amet, consectetur adipiscing elit, sed do eiusmod tempor incididunt ut labore et dolore</p>
  </div>
  <div class="feature" style="left:900px">
    <div class="f-icon"><svg width="40" height="40" viewBox="0 0 40 40" fill="none" stroke="#00AB8E" stroke-width="1.6"><circle cx="17" cy="22" r="10"/><circle cx="28" cy="11" r="6"/><circle cx="17" cy="22" r="4"/><circle cx="28" cy="11" r="2"/></svg></div>
    <h3 class="serif">Actual teachings of great</h3>
    <p>Lorem ipsum dolor sit amet, consectetur adipiscing elit, sed do eiusmod tempor incididunt ut labore et dolore</p>
  </div>
</section>

<section class="about">
  <div class="abs" style="left:0;top:547px;width:289px;height:80px;background:var(--green)"></div>
  <div class="abs" style="left:519px;top:123px;width:33px;height:181px;background:var(--green);clip-path:polygon(0 12%,100% 0,100% 100%,0 100%)"></div>
  <div class="abs" role="img" aria-label="Doctor reassuring a patient in a clinic" style="left:0;top:0;width:504px;height:547px;background:linear-gradient(135deg,#e4e8ea,#c9b7a4 55%,#b5663e)"></div>
  <div class="abs" role="img" aria-label="Therapist playing with a child using toy figures" style="left:289px;top:301px;width:310px;height:326px;background:linear-gradient(135deg,#f2eee8,#d9cbbd 55%,#7a9ab8);border:4px solid #fff;box-shadow:0 8px 24px rgba(0,0,0,.12)"></div>
  <div class="abs" style="left:584px;top:0;width:5px;height:230px;background:var(--green)"></div>
  <h2 class="serif">About Steady Steps</h2>
  <div class="lead">Sed ut perspiciatis unde omnis iste natus error sit</div>
  <p class="body">I must explain to you how all this mistaken idea of denouncing pleasure and praising pain was born and I will give you a complete account of the system, and expound the actual teachings of the great explorer of the truth, the master-builder of human happiness.</p>
  <ul class="ticks">
    <li><svg width="14" height="12" viewBox="0 0 14 12"><path d="M1 6l4 4 8-9" stroke="#00AB8E" stroke-width="2.4" fill="none"/></svg>Sed egestas tellus est aliquet eget tristique</li>
    <li><svg width="14" height="12" viewBox="0 0 14 12"><path d="M1 6l4 4 8-9" stroke="#00AB8E" stroke-width="2.4" fill="none"/></svg>Sit amet consectetur adipiscin elites varius monte</li>
    <li><svg width="14" height="12" viewBox="0 0 14 12"><path d="M1 6l4 4 8-9" stroke="#00AB8E" stroke-width="2.4" fill="none"/></svg>Proin ultrices massa arcu scelerisque facilisi</li>
  </ul>
  <div class="know">Something know about<br>our services</div>
  <a class="btn btn-fill" style="left:865px;top:535px;width:217px;height:50px;font-size:16px;font-weight:500">Book An Appointment</a>
</section>

<section class="offer">
  <h2 class="title serif center" style="top:14px">What We Offer</h2>
  <p class="sub center" style="top:101px">Lorem ipsum dolor sit amet, consectetur adipiscing elit, sed do eiusmod tempor incididunt ut labore et<br>dolore magna aliqua. Quis ipsum suspendisse ultrices gravida. Risus commodo viverra maece</p>
  <div class="card" style="left:112px">
    <div class="photo" role="img" aria-label="Couple sitting apart during a therapy session" style="background:linear-gradient(135deg,#c8b49c,#9c8a6e 60%,#6f6552)"></div>
    <div class="c-icon"><svg width="38" height="38" viewBox="0 0 40 40" fill="none" stroke="#fff" stroke-width="1.6"><circle cx="14" cy="12" r="5"/><circle cx="26" cy="12" r="5"/><path d="M6 32c0-6 4-10 8-10s8 4 8 10M18 32c0-6 4-10 8-10s8 4 8 10"/></svg></div>
    <h3 class="serif">Couples Therapy</h3>
    <p>Lorem ipsum dolor sit amet, consectetur adipiscing elit, sed do eiusmod</p>
    <a>View Details</a>
  </div>
  <div class="card" style="left:445px">
    <div class="photo" role="img" aria-label="Family talking with a counsellor" style="background:linear-gradient(135deg,#9fb2bf,#c9bcaa 55%,#8a6a52)"></div>
    <div class="c-icon"><svg width="38" height="38" viewBox="0 0 40 40" fill="none" stroke="#fff" stroke-width="1.6"><circle cx="20" cy="9" r="4"/><path d="M12 18l8 3 8-3M20 21v8M15 36l5-7 5 7"/><circle cx="9" cy="22" r="3"/><circle cx="31" cy="22" r="3"/></svg></div>
    <h3 class="serif">Family Counselling</h3>
    <p>Lorem ipsum dolor sit amet, consectetur adipiscing elit, sed do eiusmod</p>
    <a>View Details</a>
  </div>
  <div class="card" style="left:777px">
    <div class="photo" role="img" aria-label="Mother comforting an upset teenage daughter" style="background:linear-gradient(135deg,#b8342c,#b9a79a 45%,#e0612f)"></div>
    <div class="c-icon"><svg width="38" height="38" viewBox="0 0 40 40" fill="none" stroke="#fff" stroke-width="1.6"><circle cx="20" cy="10" r="5"/><circle cx="11" cy="24" r="4"/><circle cx="29" cy="24" r="4"/><path d="M4 36c0-4 3-7 7-7s7 3 7 7M22 36c0-4 3-7 7-7s7 3 7 7"/></svg></div>
    <h3 class="serif">Troubling Emotions</h3>
    <p>Lorem ipsum dolor sit amet, consectetur adipiscing elit, sed do eiusmod</p>
    <a>View Details</a>
  </div>
  <a class="btn btn-fill" style="left:386px;top:688px;width:203px">Book An Appointment</a>
  <a class="btn btn-line" style="left:611px;top:688px;width:203px">View All Services</a>
</section>

<section class="band" role="img" aria-label="Counselling session softly tinted in turquoise">
  <h2 class="serif center">Book An Appointment</h2>
  <p class="center">Lorem ipsum dolor sit amet, consectetur adipiscing elit, sed do eiusmod tempor incididunt ut labore et dolore<br>magna aliqua. Quis ipsum suspendisse ultrices gravida. Risus commodo viverra maece</p>
  <a class="btn btn-white" style="left:386px;top:234px;width:203px">Book An Appointment</a>
  <a class="btn" style="left:609px;top:234px;width:205px;border:2px solid #fff;color:#fff">Call Us: +1 555 010 2030</a>
</section>

<section class="team">
  <h2 class="title serif center" style="top:30px">Our Team Members</h2>
  <p class="sub center" style="top:113px">Lorem ipsum dolor sit amet, consectetur adipiscing elit, sed do eiusmod tempor incididunt</p>
  <div class="member" style="left:102px">
    <div class="photo" role="img" aria-label="Portrait of a team member" style="background:linear-gradient(160deg,#d9dcd6,#8f9a86 60%,#2e2e33)"></div>
    <div class="pill"><i></i><i></i><i></i></div>
    <h3>Jonah Whitfield</h3><span>Lorem Dummy</span>
  </div>
  <div class="member" style="left:355px">
    <div class="photo" role="img" aria-label="Portrait of a team member" style="background:linear-gradient(160deg,#ece9e3,#c9b8a2 60%,#7e95a8)"></div>
    <div class="pill"><i></i><i></i><i></i></div>
    <h3>Jonah Whitfield</h3><span>Lorem Dummy</span>
  </div>
  <div class="member" style="left:607px">
    <div class="photo" role="img" aria-label="Portrait of a team member" style="background:linear-gradient(160deg,#4a3e38,#a08878 55%,#d9c7be)"></div>
    <div class="pill"><i></i><i></i><i></i></div>
    <h3>Jonah Whitfield</h3><span>Lorem Dummy</span>
  </div>
  <div class="member" style="left:862px">
    <div class="photo" role="img" aria-label="Portrait of a team member" style="background:linear-gradient(160deg,#e7e6e2,#b8b6ae 55%,#6c6f75)"></div>
    <div class="pill"><i></i><i></i><i></i></div>
    <h3>Jonah Whitfield</h3><span>Lorem Dummy</span>
  </div>
  <a class="btn btn-fill" style="left:386px;top:536px;width:203px">Book An Appointment</a>
  <a class="btn btn-line" style="left:611px;top:536px;width:203px">View All Members</a>
</section>

<footer class="footer">
  <div class="f-brand wordmark">Steady Steps Clinic</div>
  <p class="abs" style="left:112px;top:115px;width:260px">Lorem ipsum dolor sit amet, consectetur adipiscing elit, sed do eiusmod tempor incididunt ut labore et dolore magna aliqua. Quis ipsum suspendisse</p>
  <span class="fsoc" style="left:112px"></span><span class="fsoc" style="left:150px"></span><span class="fsoc" style="left:188px"></span>
  <h4 class="serif" style="left:445px">Contact Us</h4>
  <p class="abs" style="left:445px;top:112px;width:220px;line-height:32px">14 Willow Lane, Ardent<br>318 204<br><br>hello@steadystepsclinic.com<br>+1 555 010 2030</p>
  <h4 class="serif" style="left:688px">Quick Links</h4>
  <ul style="left:688px"><li>Home</li><li>About Us</li><li>Our Services</li><li>Team</li><li>Reviews</li></ul>
  <h4 class="serif" style="left:875px">Join With Us</h4>
  <p class="abs" style="left:875px;top:112px;width:210px;line-height:32px">I must explain to you how all this mistaken idea of denouncing</p>
  <div class="email">Email Address</div>
  <div class="subscribe">Subscribe Now</div>
  <div class="copy center">(C) Copyright 2024 | All Rights Reserved</div>
</footer>

</body>
</html>
```